Brimsett Gardening Fresh New Website

We are looking to create a simple fresh website for our landscaping business. The website should appeal to a 'high end' audience. We deal with a lot of Embassies and affluent clients who have extremely large gardens that are meticulously maintained. The site is about communicating our excellent landscaping and customer service skills and encouraging new clients to reach out and engage us to take care of their gardens.

The website is basically going to be our business card, it will have almost no functionality other than two 'contact us' forms, one for smaller clients and one for more detailed projects.

The website will not have a lot of written content and will have to show photos of beautifully landscaped gardens.

The main logo in black will influence the site, however, we are open to all suggestions.

We are expecting to have the following pages:
Home Page
Services
About Us
Contact Us
Showcase (photo gallery of our work)

We need someone who can code it to wordpress and be available for minor changes over a number of days. They will be simple tweaks.

```html
<!DOCTYPE html>
<html lang="en">
<head>
<meta charset="utf-8">
<title>Brimsett Gardening — Landscaping &amp; Lawn Care</title>
<link rel="stylesheet" href="https://fonts.googleapis.com/css2?family=Cinzel:wght@400;500&family=Poppins:wght@400;500;600;800&display=swap">
<style>
:root{
  --gold:#a8782a;
  --gold-line:#c9a13a;
  --yellow:#f5d13e;
  --title-yellow:#eab73a;
  --ink:#1d1d1d;
  --text:#4a4a4a;
  --muted:#f4f4f4;
  --footer:#1c1c1c;
  --footer-text:#d8d8d8;
  --white:#ffffff;
}
*{box-sizing:border-box;margin:0;padding:0}
html,body{width:1200px;height:3940px;overflow:hidden}
body{position:relative;font-family:"Poppins",sans-serif;color:var(--text);background:var(--white)}
.abs{position:absolute}
.btn{position:absolute;display:flex;align-items:center;justify-content:center;background:var(--gold);color:var(--white);font-size:12px;font-weight:500;letter-spacing:.3px;text-transform:uppercase;border-radius:3px}

/* hero */
.hero{position:absolute;left:0;top:0;width:1200px;height:680px;background:linear-gradient(100deg,#2f3a1c 0%,#3e5a22 35%,#4e7a2a 60%,#2c4a1a 100%)}
.hero-shade{position:absolute;inset:0;background:linear-gradient(90deg,rgba(0,0,0,.45),rgba(0,0,0,.05) 65%)}
.hero-curve{position:absolute;left:0;top:600px}
.nav-line{position:absolute;left:0;width:1200px;height:1px;background:var(--gold-line)}
.nav a{position:absolute;top:65px;color:var(--white);font-size:14px;text-decoration:none}
.brand-badge{position:absolute;left:539px;top:14px;width:122px;height:122px;border-radius:50%;border:2px solid var(--gold-line);background:#1f2414;display:flex;flex-direction:column;align-items:center;justify-content:center;font-family:"Cinzel",serif;color:var(--gold-line);font-size:11px;letter-spacing:2px;line-height:1.5;text-align:center}
.btn.nav-cta{left:948px;top:57px;width:110px;height:38px;background:var(--yellow);color:var(--ink);border-radius:4px;box-shadow:0 2px 6px rgba(0,0,0,.25)}
.hero h1{position:absolute;left:141px;top:246px;font-family:"Poppins",sans-serif;font-weight:800;font-size:48px;line-height:54px;color:var(--white);text-transform:uppercase}
.hero h1 .accent{color:var(--title-yellow)}
.hero p{position:absolute;left:141px;top:416px;width:520px;font-size:13px;line-height:23px;color:var(--white)}
.btn.hero-cta{left:141px;top:486px;width:111px;height:37px}
.scroll-cue{position:absolute;left:568px;top:598px;width:64px;height:64px;border-radius:50%;background:var(--white);box-shadow:0 4px 14px rgba(0,0,0,.18);display:flex;align-items:center;justify-content:center}

/* about */
.about-photo{left:119px;top:700px;width:485px;height:447px;background:linear-gradient(180deg,#e9ecef 0%,#c7ccd2 55%,#8fa07a 100%);border-radius:2px}
.section-kicker{font-family:"Cinzel",serif;font-size:35px;color:var(--gold);line-height:1}
.section-title{font-family:"Cinzel",serif;font-size:35px;color:var(--ink);line-height:1}
.rule{position:absolute;height:2px;width:50px;background:var(--gold)}
.about-copy{left:612px;top:906px;width:450px;font-size:13px;line-height:21.5px}
.about-copy p+p{margin-top:7px}

/* services */
.services{position:absolute;left:0;top:1214px;width:1200px;height:946px;background:var(--muted)}
.center-title{position:absolute;left:0;width:1200px;text-align:center;font-family:"Cinzel",serif;font-size:36px;color:var(--ink)}
.tab{position:absolute;top:1370px;height:34px;display:flex;align-items:center;justify-content:center;font-size:12px;font-weight:500;border-radius:2px}
.tab.active{left:439px;width:157px;background:var(--yellow);color:var(--ink)}
.tab.idle{left:604px;width:157px;background:var(--gold);color:var(--white)}
.card{position:absolute;width:300px;height:241px;border-radius:4px;overflow:hidden}
.card .photo{position:absolute;inset:0}
.card .fade{position:absolute;inset:0;background:linear-gradient(180deg,rgba(0,0,0,0) 45%,rgba(0,0,0,.8) 100%)}
.card .label{position:absolute;left:0;right:0;bottom:26px;display:flex;align-items:center;justify-content:center;gap:8px;color:var(--white);font-size:15px;font-weight:500}
.card .label small{display:block;font-size:12px;text-decoration:underline;margin-top:2px}

/* testimonials */
.reviews{position:absolute;left:0;top:2160px;width:1200px;height:534px;background:linear-gradient(120deg,#3d3d38 0%,#4b5036 40%,#2e3527 100%)}
.reviews .veil{position:absolute;inset:0;background:rgba(0,0,0,.35)}
.review{position:absolute;width:300px;background:var(--white);border-radius:4px;padding:22px 22px}
.review .who{display:flex;align-items:center;gap:12px;margin-bottom:18px}
.avatar{width:58px;height:58px;border-radius:50%}
.review .name{font-size:15px;font-weight:500;color:var(--ink)}
.stars{color:var(--yellow);font-size:13px;letter-spacing:2px}
.review p{font-size:12.5px;line-height:21.5px}
.review.featured{border-bottom:6px solid var(--gold)}
.arrow{position:absolute;top:2473px;width:44px;height:44px;border-radius:50%;border:2px solid var(--white);display:flex;align-items:center;justify-content:center}

/* gallery */
.tile{position:absolute;width:300px;height:267px}
.tile.note{background:var(--yellow);display:flex;align-items:center;justify-content:center;text-align:center;padding:0 56px;font-size:13px;line-height:21.5px;color:var(--ink)}

/* footer */
.footer{position:absolute;left:0;top:3562px;width:1200px;height:378px;background:var(--footer)}
.foot-brand{position:absolute;left:120px;top:3712px;width:230px;text-align:center;font-family:"Cinzel",serif;color:var(--title-yellow);font-size:26px;letter-spacing:8px;line-height:1.4}
.foot-brand span{display:block;font-size:16px;letter-spacing:9px}
.social{position:absolute;top:3811px;width:27px;height:27px;border-radius:50%;border:1.5px solid var(--footer-text)}
.foot-head{position:absolute;top:3614px;font-family:"Cinzel",serif;font-size:17px;color:#e6e6e6;letter-spacing:.5px}
.foot-link{position:absolute;left:518px;font-size:13px;color:var(--footer-text)}
.contact-row{position:absolute;left:849px;display:flex;gap:10px;align-items:flex-start;font-size:13px;line-height:18px;color:var(--footer-text)}
.contact-row b{font-weight:500;display:block}
.foot-rule{position:absolute;left:141px;top:3896px;width:917px;height:1px;background:#4a4a4a}
.copyright{position:absolute;left:0;top:3908px;width:1200px;text-align:center;font-size:12px;color:var(--footer-text)}
</style>
</head>
<body>

<!-- HERO -->
<section class="hero">
  <div role="img" aria-label="Manicured estate lawn with sculpted shrubs and trees" class="abs" style="inset:0"></div>
  <div class="hero-shade"></div>
  <div class="nav-line" style="top:46px"></div>
  <div class="nav-line" style="top:106px"></div>
  <nav class="nav">
    <a style="left:140px">Home</a>
    <a style="left:262px">About Us</a>
    <a style="left:409px">Services</a>
    <a style="left:726px">Our Gallery</a>
  </nav>
  <div class="brand-badge">BRIMSETT<br><span style="font-size:8px;letter-spacing:3px">GARDENING</span></div>
  <div class="btn nav-cta">Contact Us</div>
  <h1><span class="accent">Brimsett Gardening</span><br>Your Full Landscaping<br>&amp; Lawn Care Experts</h1>
  <p>Lorem ipsum dolor sit amet, consectetur adipiscing elit, sed do eiusmod tempor incididunt ut labore et dolore magna aliqua.</p>
  <div class="btn hero-cta">Read More</div>
  <svg class="hero-curve" width="1200" height="82" viewBox="0 0 1200 82"><path d="M0 72 Q600 -10 1200 72 L1200 82 L0 82Z" fill="#fff"/></svg>
  <div class="scroll-cue"><svg width="22" height="34" viewBox="0 0 22 34"><rect x="2" y="2" width="18" height="30" rx="9" fill="none" stroke="#1d1d1d" stroke-width="2.2"/><line x1="11" y1="8" x2="11" y2="14" stroke="#1d1d1d" stroke-width="2.2" stroke-linecap="round"/></svg></div>
</section>

<!-- ABOUT -->
<div role="img" aria-label="Large white country house with porch" class="abs about-photo"></div>
<div class="abs" style="left:612px;top:797px">
  <div class="section-kicker">ABOUT</div>
  <div class="section-title" style="margin-top:5px">BRIMSETT GARDENING</div>
</div>
<div class="rule" style="left:612px;top:884px"></div>
<div class="abs about-copy">
  <p>Duis aute irure dolor in reprehenderit in voluptate velit esse cillum dolore eu fugiat nulla pariatur.</p>
  <p>Lorem ipsum dolor sit amet, consectetur adipiscing elit, sed do amit eiusmod tempor incididunt ut labore et dolore magna aliqua. Ut enim ad minim veniam, quis nostrud exercitation ullamco laboris nisi ut aliquip ex ea commodo consequat.</p>
</div>
<div class="btn" style="left:612px;top:1064px;width:153px;height:34px">Read More</div>

<!-- SERVICES -->
<section class="services"></section>
<div class="center-title" style="top:1290px">OUR SERVICES</div>
<div class="rule" style="left:575px;top:1346px"></div>
<div class="tab active">LANDSCAPE SERVICE</div>
<div class="tab idle">LAWN SERVICE</div>

<div class="card" style="left:141px;top:1436px"><div role="img" aria-label="Stately home behind green trees and lawn" class="photo" style="background:linear-gradient(180deg,#9fb9d4 0%,#5f7f4a 55%,#2f4a22 100%)"></div><div class="fade"></div><div class="label"><svg width="34" height="34"><rect x="3" y="3" width="28" height="28" fill="none" stroke="#fff" stroke-width="2"/><rect x="6" y="6" width="10" height="10" fill="#f5d13e"/></svg>Design Service</div></div>
<div class="card" style="left:450px;top:1436px"><div role="img" aria-label="Tree-shaded garden with mulch beds" class="photo" style="background:linear-gradient(180deg,#8aa070 0%,#4f6a36 55%,#2d3a22 100%)"></div><div class="fade"></div><div class="label" style="bottom:18px"><svg width="34" height="34"><circle cx="24" cy="24" r="7" fill="none" stroke="#fff" stroke-width="2"/><path d="M3 12 H22 L26 18" fill="none" stroke="#fff" stroke-width="2"/></svg><div>Mulch or Rock Install<small>Get A Estimate →</small></div></div></div>
<div class="card" style="left:758px;top:1436px"><div role="img" aria-label="Dark soil with trowel and potted seedlings" class="photo" style="background:linear-gradient(160deg,#5a4636 0%,#3b2c22 60%,#251b14 100%)"></div><div class="fade"></div><div class="label"><svg width="34" height="34"><path d="M4 30 L30 30 M8 30 L20 14 M20 14 L28 6" fill="none" stroke="#f5d13e" stroke-width="2.2"/></svg>Grading Rough</div></div>

<div class="card" style="left:141px;top:1752px"><div role="img" aria-label="White manor house beyond a wide lawn" class="photo" style="background:linear-gradient(180deg,#cfd7df 0%,#6f8a5a 50%,#2e4322 100%)"></div><div class="fade"></div><div class="label"><svg width="28" height="34"><rect x="4" y="4" width="20" height="27" rx="2" fill="none" stroke="#fff" stroke-width="2"/><line x1="8" y1="12" x2="20" y2="12" stroke="#f5d13e" stroke-width="2"/><line x1="8" y1="18" x2="20" y2="18" stroke="#fff" stroke-width="2"/><line x1="8" y1="24" x2="20" y2="24" stroke="#fff" stroke-width="2"/></svg>Grading Final</div></div>
<div class="card" style="left:450px;top:1752px"><div role="img" aria-label="Rolls of fresh sod being laid on a lawn" class="photo" style="background:linear-gradient(180deg,#6f7a52 0%,#6b5a3a 50%,#3f5a28 100%)"></div><div class="fade"></div><div class="label"><svg width="34" height="34"><rect x="3" y="6" width="22" height="22" fill="none" stroke="#fff" stroke-width="2"/><circle cx="26" cy="24" r="5" fill="#f5d13e"/></svg>Sod Installation</div></div>
<div class="card" style="left:758px;top:1752px"><div role="img" aria-label="Hedged garden path with iron railing" class="photo" style="background:linear-gradient(180deg,#a9b4a3 0%,#4d6a3a 50%,#26361c 100%)"></div><div class="fade"></div><div class="label"><svg width="50" height="34"><rect x="2" y="4" width="46" height="26" fill="#fff"/><g stroke="#1d1d1d" stroke-width="2"><line x1="2" y1="13" x2="48" y2="13"/><line x1="2" y1="21" x2="48" y2="21"/><line x1="16" y1="4" x2="16" y2="13"/><line x1="32" y1="4" x2="32" y2="13"/><line x1="24" y1="13" x2="24" y2="21"/><line x1="16" y1="21" x2="16" y2="30"/><line x1="32" y1="21" x2="32" y2="30"/></g><rect x="4" y="6" width="10" height="5" fill="#f5d13e"/></svg>Retaining Walls</div></div>

<div class="btn" style="left:523px;top:2041px;width:153px;height:34px">Request A Quote</div>

<!-- TESTIMONIALS -->
<section class="reviews" role="img" aria-label="Dusky garden terrace with trees and benches"><div class="veil"></div></section>
<div class="center-title" style="top:2234px;color:#fff">WHAT OUR CLIENTS SAY</div>

<div class="arrow" style="left:74px"><svg width="12" height="16"><path d="M9 2 L3 8 L9 14" fill="none" stroke="#fff" stroke-width="2"/></svg></div>
<div class="arrow" style="left:1082px"><svg width="12" height="16"><path d="M3 2 L9 8 L3 14" fill="none" stroke="#fff" stroke-width="2"/></svg></div>

<div class="review" style="left:141px;top:2342px;height:266px">
  <div class="who"><div role="img" aria-label="Client portrait" class="avatar" style="background:#6fa3c4"></div><div><div class="name">Owen Carrow</div><div class="stars">★★★★★</div></div></div>
  <p>Lorem ipsum dolor sit amet, consectetur adipiscing elit, sed do eiusmod tempor incididunt ut labore et dolore magna aliqua. Ut enim ad minim veniam ut aut reiciendis voluptatibus maiores alias ut aut reiciendis voluptatibus.</p>
</div>
<div class="review featured" style="left:450px;top:2313px;height:271px">
  <div class="who"><div role="img" aria-label="Client portrait" class="avatar" style="background:#7d6a5c"></div><div><div class="name">Tessa Marlow</div><div class="stars">★★★★★</div></div></div>
  <p>Sed ut perspiciatis unde omnis iste natus error sit voluptatem accusantium doloremque laudantium, totam rem aperiam, eaque ipsa quae ab illo AMIT inventore veritatis et quasi architecto beatae vitae dicta sunt explicabo. Nemo enim ipsam voluptatem.</p>
</div>
<div class="review" style="left:758px;top:2342px;height:266px">
  <div class="who"><div role="img" aria-label="Client portrait" class="avatar" style="background:#3b4a3a"></div><div><div class="name">Ravi P</div><div class="stars">★★★★★</div></div></div>
  <p>Lorem ipsum dolor sit amet, consectetur adipiscing elit, sed do eiusmod tempor incididunt ut labore et dolore magna aliqua. Ut enim ad minim veniam ut aut reiciendis voluptatibus maiores alias ut aut reiciendis voluptatibus.</p>
</div>

<!-- GALLERY -->
<div class="center-title" style="top:2766px">WORK GALLERY</div>
<div class="rule" style="left:575px;top:2822px"></div>

<div role="img" aria-label="Cottage with flowering front garden" class="tile" style="left:141px;top:2876px;background:linear-gradient(180deg,#b8c4cf 0%,#a58f72 45%,#6a7c4a 100%)"></div>
<div role="img" aria-label="Garden pavilion beneath tall trees" class="tile" style="left:141px;top:3151px;background:linear-gradient(180deg,#5f7a42 0%,#3e5a2a 60%,#6c6a5a 100%)"></div>
<div class="tile note" style="left:450px;top:2847px">Itaque earum rerum hic tenetur a sapiente delectus, ut aut reiciendis voluptatibus maiores alias consequatur aut perferendis doloribus asperiores repellat.</div>
<div role="img" aria-label="Stone steps through colourful flower beds" class="tile" style="left:450px;top:3124px;background:linear-gradient(180deg,#7a4a52 0%,#5f7a3e 35%,#8a7d70 100%)"></div>
<div role="img" aria-label="Hillside homes above a sunlit lawn" class="tile" style="left:758px;top:2876px;background:linear-gradient(180deg,#c6d6e2 0%,#8a9a6a 45%,#5f9a2e 100%)"></div>
<div role="img" aria-label="Checkered stone path to a house" class="tile" style="left:758px;top:3151px;background:linear-gradient(180deg,#8a9c70 0%,#4a6a2c 55%,#7d7a6e 100%)"></div>

<div class="btn" style="left:523px;top:3440px;width:153px;height:35px">View All</div>

<!-- FOOTER -->
<footer class="footer"></footer>
<div class="foot-brand">BRIMSETT<span>GARDENING</span></div>
<div class="social" style="left:169px"></div>
<div class="social" style="left:204px"></div>
<div class="social" style="left:239px"></div>
<div class="social" style="left:273px"></div>

<div class="foot-head" style="left:518px">QUICK LINKS</div>
<div class="rule" style="left:518px;top:3644px;width:48px"></div>
<div class="foot-link" style="top:3664px">Home</div>
<div class="foot-link" style="top:3704px">Services</div>
<div class="foot-link" style="top:3745px">Gallery</div>
<div class="foot-link" style="top:3786px">About Us</div>
<div class="foot-link" style="top:3826px">contact Us</div>

<div class="foot-head" style="left:849px">CONTACT DETAILS</div>
<div class="rule" style="left:849px;top:3644px;width:48px"></div>
<div class="contact-row" style="top:3658px"><svg width="28" height="30"><path d="M14 3 C8 3 4 7 4 12 C4 19 14 27 14 27 C14 27 24 19 24 12 C24 7 20 3 14 3Z" fill="none" stroke="#d8d8d8" stroke-width="1.8"/><circle cx="14" cy="12" r="3.5" fill="none" stroke="#d8d8d8" stroke-width="1.8"/></svg><div>123, Building Name, Street<br>City, State XY 123456</div></div>
<div class="contact-row" style="top:3730px"><svg width="28" height="30"><path d="M7 4 L12 4 L14 10 L11 13 C13 17 15 19 19 21 L22 18 L28 20 L28 25 C28 27 26 28 24 28 C13 27 4 18 3 8 C3 6 5 4 7 4Z" fill="none" stroke="#d8d8d8" stroke-width="1.8"/></svg><div><b>Phone</b>(123) 456-7890</div></div>
<div class="contact-row" style="top:3803px"><svg width="28" height="30"><rect x="3" y="7" width="22" height="17" fill="none" stroke="#d8d8d8" stroke-width="1.8"/><path d="M3 7 L14 17 L25 7" fill="none" stroke="#d8d8d8" stroke-width="1.8"/></svg><div><b>Email</b>info@brimsettgardening.com</div></div>

<div class="foot-rule"></div>
<div class="copyright">© 2024 Brimsett Gardening. All Rights Reserved</div>

</body>
</html>
```